Photography business - business card design quick turn around

Create a business card design for me please. I actually need the final design back before the end of Sunday 13th May 7pm GMT. Sorry for the short notice.

Photoshop artwork template uploaded with artwork guidelines including printer profiles and other mandatory specifications. Only one side of the business card is required as the other side will be an image.

The design is required as an unflattened PSD file so that I can edit the text if I need to.

My brand colours are white and the teal you see in the logo. Occasionally I also use a dark grey on my website (I don't mind the shade of grey as appreciate grey on teal would be a different grey, to the grey I use on white on the website, so just use a shade of grey that matches). Font can be as the font for the logo or if you prefer I am open to another sans serif, easily legible font. Ideally font size will be 12+.Please do not use capital letters for text. I prefer everything to be lower case, if possible.

Thank you.

Lena

Target Market(s)

Other business owners who may refer me and families

Industry/Entity Type

Photographer

Contact Information for Business Card

Silver Kettle Photography Logo
Sub text: family portraiture, captured with love

Contact information, ideally using simple icons to represent email / website / facebook / instagram / pinterest

email: lena@silverkettlephotography.co.uk
website: silverkettlephotography.co.uk
facebook: @silverkettlephotography
pinterest: pinterest.com/silverkettlepho
instagram: @silverkettle_photography
mobile/telephone: 07713460291

If there is too much text then please drop the instagram and pinterest information.

Font styles to use
Sans Serif

Colors
33b8a4

Requirements
Must have
• Logo
• Contact details as listed above
• sub text
Nice to have
• Instagram and Pinterest contact details
• Nice to have icons to represent website / phone / facebook etc followered by the handle where relevant

```html
<!DOCTYPE html>
<html lang="en">
<head>
<meta charset="utf-8">
<title>Silver Kettle Photography – business card</title>
<link rel="stylesheet" href="https://fonts.googleapis.com/css2?family=Mulish:wght@400;700&display=swap">
<style>
  :root {
    --backdrop: #2b2b2b;
    --card: #5b5b5b;
    --teal: #2fd2bd;
    --white: #ffffff;
    --soft-white: #e4e4e4;
    --icon-glyph: #4a4a4a;
  }
  * { box-sizing: border-box; margin: 0; padding: 0; }
  html, body {
    width: 1200px;
    height: 1000px;
    overflow: hidden;
    background: var(--backdrop);
  }
  .business-card {
    position: absolute;
    left: 100px;
    top: 215px;
    width: 1000px;
    height: 570px;
    border-radius: 40px;
    background: var(--card);
    font-family: "Mulish", sans-serif;
  }
  .brand-block {
    position: absolute;
    left: 90px;
    top: 150px;
    width: 340px;
  }
  .brand-mark {
    width: 120px;
    height: 120px;
    margin: 0 auto 26px;
    border-radius: 50%;
    background: var(--teal);
  }
  .brand-name {
    color: var(--teal);
    font-weight: 400;
    font-size: 34px;
    line-height: 1.05;
    letter-spacing: 1px;
    text-align: center;
  }
  .brand-rule {
    height: 2px;
    background: var(--soft-white);
    margin: 12px 0 8px;
  }
  .brand-tagline {
    color: var(--soft-white);
    font-size: 17px;
    font-weight: 400;
    text-align: center;
  }
  .divider {
    position: absolute;
    left: 468px;
    top: 140px;
    width: 2px;
    height: 290px;
    background: var(--soft-white);
    transform: rotate(8deg);
  }
  .contact-list {
    position: absolute;
    left: 520px;
    top: 160px;
    list-style: none;
  }
  .contact-item {
    display: flex;
    align-items: center;
    gap: 12px;
    height: 42px;
    color: var(--white);
    font-weight: 700;
    font-size: 24px;
  }
  .contact-icon {
    width: 28px;
    height: 28px;
    flex: none;
  }
  .contact-icon .badge { fill: var(--teal); }
  .contact-icon .glyph { fill: var(--icon-glyph); }
  .contact-icon .glyph-line { fill: none; stroke: var(--icon-glyph); stroke-width: 1.8; }
</style>
</head>
<body>
  <div class="business-card">
    <div class="brand-block">
      <div class="brand-mark"></div>
      <p class="brand-name">silver kettle<br>photography</p>
      <div class="brand-rule"></div>
      <p class="brand-tagline">family portraiture, captured with love</p>
    </div>

    <div class="divider"></div>

    <ul class="contact-list">
      <li class="contact-item">
        <svg class="contact-icon" viewBox="0 0 28 28" aria-hidden="true">
          <circle class="badge" cx="14" cy="14" r="14"/>
          <path class="glyph" d="M9 7.5l3 3-1.6 1.8c.9 1.9 2.4 3.4 4.3 4.3l1.8-1.6 3 3-1.8 2c-5.6-.6-10.1-5.1-10.7-10.7z"/>
        </svg>
        07713460291
      </li>
      <li class="contact-item">
        <svg class="contact-icon" viewBox="0 0 28 28" aria-hidden="true">
          <circle class="badge" cx="14" cy="14" r="14"/>
          <rect class="glyph-line" x="7.5" y="9" width="13" height="10" rx="1"/>
          <path class="glyph-line" d="M7.5 9.5l6.5 5 6.5-5"/>
        </svg>
        lena@silverkettlephotography.co.uk
      </li>
      <li class="contact-item">
        <svg class="contact-icon" viewBox="0 0 28 28" aria-hidden="true">
          <circle class="badge" cx="14" cy="14" r="14"/>
          <circle class="glyph-line" cx="14" cy="14" r="7"/>
          <ellipse class="glyph-line" cx="14" cy="14" rx="3" ry="7"/>
          <path class="glyph-line" d="M7 14h14"/>
        </svg>
        silverkettlephotography.co.uk
      </li>
      <li class="contact-item">
        <svg class="contact-icon" viewBox="0 0 28 28" aria-hidden="true">
          <circle class="badge" cx="14" cy="14" r="14"/>
        </svg>
        @silverkettlephotography
      </li>
      <li class="contact-item">
        <svg class="contact-icon" viewBox="0 0 28 28" aria-hidden="true">
          <circle class="badge" cx="14" cy="14" r="14"/>
        </svg>
        silverkettlepho
      </li>
      <li class="contact-item">
        <svg class="contact-icon" viewBox="0 0 28 28" aria-hidden="true">
          <circle class="badge" cx="14" cy="14" r="14"/>
        </svg>
        @silverkettle_photography
      </li>
    </ul>
  </div>
</body>
</html>
```